Need to drive pregnant women to my 3d4d ultrasound studio where i provide 4d ultrasound with hyperalistic imaging and gender reveals

Industry/Entity Type

Healthcare

Font styles to use
Decorative
Script

Requirements
Must have
• My Company name Cielo de Nuestra Espera 4D. EVERYTHING HAS TO BE IN SPANISH
Nice to have
• SIMPLE AND NOT TOO BUSY
Should not have
• website

```html
<!DOCTYPE html>
<html lang="es">
<head>
<meta charset="utf-8">
<title>Cielo de Nuestra Espera 4D – Banner</title>
<link rel="stylesheet" href="https://fonts.googleapis.com/css2?family=Dancing+Script:wght@700&family=Lilita+One&display=swap">
<style>
  :root {
    --backdrop: #a0a0a0;
    --paper: #ffffff;
    --ink: #000000;
    --panel-dark: #050505;
    --panel-sheen: #4a4a4c;
    --ring: #c9c9c9;
    --scan-light: #c77a2e;
    --scan-dark: #7a3e10;
    --skin-light: #e8bca8;
    --skin-dark: #c68a78;
  }
  * { margin: 0; padding: 0; box-sizing: border-box; }
  html, body { width: 1200px; height: 600px; overflow: hidden; background: var(--backdrop); }
  .banner {
    position: absolute; left: 79px; top: 154px; width: 1043px; height: 304px;
    background: var(--paper);
    box-shadow: 0 1px 3px rgba(0,0,0,.35);
    overflow: hidden;
  }
  .banner-art { position: absolute; inset: 0; }
  .title { font-weight: 400; }
  .title-top, .title-main {
    position: absolute; display: flex; align-items: center; justify-content: center;
    font-family: "Lilita One", "Arial Black", sans-serif;
    line-height: 1; white-space: nowrap;
  }
  .title-top {
    left: 41px; top: 28px; width: 453px; height: 52px;
    font-size: 44px; letter-spacing: 1px; color: var(--ink);
  }
  .title-main {
    left: 41px; top: 84px; width: 453px; height: 93px;
    font-size: 78px; letter-spacing: 2px; color: var(--paper);
    padding-top: 4px;
  }
  .tagline {
    position: absolute; left: 41px; top: 196px; width: 453px;
    font-family: "Dancing Script", cursive;
    font-weight: 700; font-size: 34px; line-height: 42px;
    color: var(--ink); text-align: center;
  }
</style>
</head>
<body>
  <div class="banner">
    <svg class="banner-art" width="1043" height="304" viewBox="0 0 1043 304">
      <defs>
        <linearGradient id="panelGradient" x1="0" y1="0" x2="1" y2="1">
          <stop offset="0" stop-color="#050505"/>
          <stop offset="0.3" stop-color="#4a4a4c"/>
          <stop offset="0.55" stop-color="#050505"/>
          <stop offset="0.85" stop-color="#4a4a4c"/>
          <stop offset="1" stop-color="#050505"/>
        </linearGradient>
        <radialGradient id="scanGradient" cx="0.45" cy="0.45" r="0.6">
          <stop offset="0" stop-color="#c77a2e"/>
          <stop offset="1" stop-color="#7a3e10"/>
        </radialGradient>
        <radialGradient id="newbornGradient" cx="0.5" cy="0.5" r="0.6">
          <stop offset="0" stop-color="#e8bca8"/>
          <stop offset="1" stop-color="#c68a78"/>
        </radialGradient>
      </defs>
      <path class="title-band" d="M41 84 H448 A46.5 46.5 0 0 1 448 177 H71 Z" fill="#000000"/>
      <path class="image-panel" d="M686 0 H1043 V304 H686 A152 152 0 0 1 686 0 Z" fill="url(#panelGradient)"/>
      <g class="image-frame">
        <circle cx="680" cy="150" r="108" fill="url(#scanGradient)" role="img" aria-label="Imagen de ecografía 4D del bebé en el vientre"/>
        <circle cx="680" cy="150" r="108" fill="none" stroke="#c9c9c9" stroke-width="4"/>
      </g>
      <g class="image-frame">
        <circle cx="909" cy="150" r="108" fill="url(#newbornGradient)" role="img" aria-label="Fotografía del bebé recién nacido dormido"/>
        <circle cx="909" cy="150" r="108" fill="none" stroke="#c9c9c9" stroke-width="4"/>
      </g>
    </svg>
    <h1 class="title">
      <span class="title-top">CIELO DE NUESTRA</span>
      <span class="title-main">ESPERA 4D</span>
    </h1>
    <p class="tagline">Ecografía 4D hiperrealista<br>y revelación de sexo</p>
  </div>
</body>
</html>
```